Elegant and modern Wedding Photography brochure

My existing brochure (attached) needs a major facelift. This is one of the main selling tools - it gets emailed to my clients when they make an equiry on what packages i offer and it is printed out and walked through at our first meeting. This brochure is as critical as my website - it needs to sing!

I'm looking for an eye-catching design that says:
Elegant
Modern
Clean
Crisp
Not cutesy or lovey-dovey thanks - we are more sophisticated and professional than that.

Update images to some of the latest weddings I've shot also. Let me know files and resolution you need. I've enabled right-click to download images on my site for a limited time. Please note that I retain copyright and will pursue any breeches.

Http://www.sarahkelbrin.com/Melbourne-wedding-photography
Updates

Thanks for all of your designs! Will take a few days to decide.

Target Market(s)

Australian Women aged 24-44

Industry/Entity Type

Wedding

Font styles to use
Other font styles liked:
• Century Gothic

Requirements
Must have
• Easy to print - does not have to be 6 A4 pages like the existing brochure
Nice to have
• Some full page images - The photos are supposed to be the hero here :-)
Should not have
• Not cutesy or lovey-dovey thanks - we are more sophisticated and professional than that.

No black backgrounds, I prefer a white thanks

No images in organic shaped boxes (like the rectangles in the logo - no thanks).
Keep the lines straight and sharp

```html
<!DOCTYPE html>
<html lang="en">
<head>
<meta charset="utf-8">
<title>Wedding Packages – Pricelist 2013</title>
<link rel="stylesheet" href="https://fonts.googleapis.com/css2?family=Questrial&family=Urbanist:wght@700;800&display=swap">
<style>
  :root {
    --plum: #8b2b8c;
    --ink: #222222;
    --paper: #ffffff;
    --photo-dark: #2f2b2c;
    --photo-green: #5d6b4c;
    --photo-cream: #d3c8b4;
  }
  * { box-sizing: border-box; margin: 0; padding: 0; }
  html, body { width: 1200px; height: 856px; overflow: hidden; background: var(--paper); }
  body { font-family: "Questrial", "Century Gothic", sans-serif; color: var(--ink); }
  .page { position: relative; width: 1200px; height: 856px; }

  .title-block { position: absolute; left: 58px; top: 52px; }
  .title { font-family: "Urbanist", "Century Gothic", sans-serif; font-size: 43px; font-weight: 800; color: var(--plum); line-height: 1; }
  .subtitle { font-size: 19px; line-height: 1; margin-top: 3px; }

  .hero {
    position: absolute; left: 0; top: 134px; width: 1200px; height: 138px;
    background: linear-gradient(90deg, var(--photo-green) 0%, #3d4535 30%, var(--photo-dark) 48%, var(--photo-cream) 62%, #a8a08c 78%, var(--photo-green) 100%);
  }

  .photo { position: absolute; left: 58px; width: 238px; height: 158px; }
  .photo-1 { top: 293px; background: linear-gradient(100deg, var(--photo-dark) 0%, var(--photo-green) 45%, #c9c0ad 80%, #9c927c 100%); }
  .photo-2 { top: 458px; background: linear-gradient(90deg, var(--photo-green) 0%, var(--photo-dark) 35%, #b7ad9b 60%, #6c7558 100%); }
  .photo-3 { top: 624px; background: linear-gradient(90deg, #3f6a4a 0%, var(--photo-dark) 35%, #d8cdb9 65%, #a98b5f 100%); }

  .package { position: absolute; top: 291px; font-size: 13.4px; line-height: 15.3px; white-space: nowrap; }
  .package-signature { left: 344px; }
  .package-platinum { left: 651px; }
  .package-gold { left: 910px; }
  .package-name, .package-price { font-family: "Urbanist", "Century Gothic", sans-serif; font-weight: 700; color: var(--plum); }
  .package-name { font-size: 16px; letter-spacing: 0.4px; line-height: 18px; margin-bottom: 18px; }
  .package-price { font-size: 14.5px; line-height: 17px; margin-bottom: 15px; }
  .package p { margin-bottom: 15.3px; }
  .package p.tight { margin-bottom: 0; }

  .footer-contact { position: absolute; right: 48px; top: 786px; font-size: 13.5px; color: var(--plum); display: flex; align-items: center; gap: 9px; }
  .separator { width: 5px; height: 5px; border-radius: 50%; background: var(--plum); }
  .footer-rule { position: absolute; left: 58px; top: 817px; width: 1094px; height: 4px; background: var(--plum); }
</style>
</head>
<body>
<main class="page">
  <header class="title-block">
    <h1 class="title">Wedding Packages</h1>
    <p class="subtitle">Pricelist 2013</p>
  </header>

  <div class="hero" role="img" aria-label="Full-width hero photograph of a recent wedding couple in a park"></div>

  <div class="photo photo-1" role="img" aria-label="Bride in a white dress leaning against a tree, groom blurred in the foreground"></div>
  <div class="photo photo-2" role="img" aria-label="Couple standing together beneath park trees"></div>
  <div class="photo photo-3" role="img" aria-label="Couple embracing in front of a graffiti wall"></div>

  <section class="package package-signature">
    <h2 class="package-name">SIGNATURE</h2>
    <div class="package-price">Price: $3650<br>($5540 value)</div>
    <p>Up to 8 hrs of coverage</p>
    <p>Signature Grand (A3) Album<br>with Lay-flat 300g paper, frosted<br>page, choice of premium linen<br>or leather cover, presentation<br>box, name embossing, up to 52<br>pages</p>
    <p>Custom Thank-you Cards with<br>envelopes (50)</p>
    <p>Client for life (no sitting fees)</p>
    <p>Second photographer</p>
    <p>Fusion Slideshow (still + moving<br>images)</p>
    <p class="tight">Pre-wedding Shoot</p>
    <p>Web Gallery (online for 6 weeks)<br>&amp; Social media</p>
    <p>High Resolution Digital<br>Negatives*</p>
  </section>

  <section class="package package-platinum">
    <h2 class="package-name">PLATINUM</h2>
    <div class="package-price">Price: $2300<br>($3440 value)</div>
    <p>Up to 6 hrs of coverage</p>
    <p>Regular (A4) Album with Lay-flat<br>300g paper, printed cover, dust<br>jacket, presentation box, up to<br>42 pages</p>
    <p>Slideshow</p>
    <p>Pre-wedding shoot</p>
    <p>Web Gallery (online for 6 weeks)<br>&amp; Social media</p>
    <p>High Resolution Digital<br>Negatives*</p>
  </section>

  <section class="package package-gold">
    <h2 class="package-name">GOLD</h2>
    <div class="package-price">Price: $1650<br>($2080 value)</div>
    <p>Up to 4 hrs of coverage</p>
    <p>Regular (A4) Album with Lay-flat 300g<br>paper, printed cover, dust jacket,<br>presentation box, up to<br>32 pages</p>
    <p>Web Gallery (online for 6 weeks)&amp;<br>Social media</p>
    <p>High Resolution Digital<br>Negatives*</p>
  </section>

  <footer>
    <div class="footer-contact">
      <span>www.sarahkelbrin.com</span>
      <span class="separator"></span>
      <span>Mobile: 0400 555 218 7</span>
      <span class="separator"></span>
      <span>Email: hello@sarahkelbrin.com</span>
    </div>
    <div class="footer-rule"></div>
  </footer>
</main>
</body>
</html>
```